BRIGHTHOLD PROPERTY MANAGEMENT INC. WEBSITE

Please make the website more family-friendly.

I want a website to help me build my property management business by adding listing properties and creating an online application. Im open to any other ideas.
I want a WordPress designer to code it.

Here is my current website. www.brighthold.biz

IDEA: I like the website design https://www.pelicanclimateservices.com/

Thank you

Tom

Number of Pages Required

5+ page

```html
<!DOCTYPE html>
<html lang="en">
<head>
<meta charset="utf-8">
<title>Brighthold Property Management</title>
<link rel="stylesheet" href="https://fonts.googleapis.com/css2?family=Cinzel:wght@500;600;700&family=Poppins:wght@400;500;600&family=Nunito+Sans:wght@400;600;700&display=swap">
<style>
:root{
  --red:#9e1016;
  --red-dark:#7f0c11;
  --ink:#222;
  --dark:#262626;
  --text:#444;
  --muted:#8a8a8a;
  --pink:#f1e4e5;
  --white:#fff;
}
*{box-sizing:border-box;margin:0;padding:0}
html,body{width:1200px;height:2979px;overflow:hidden;background:#fff}
body{position:relative;font-family:"Nunito Sans",sans-serif;color:var(--ink)}
.abs{position:absolute}

/* header */
.brand{left:120px;top:22px;width:190px;height:100px;display:flex;flex-direction:column;align-items:center;justify-content:center;gap:8px}
.brand-mark{width:34px;height:34px;background:var(--ink)}
.brand-name{font-family:"Cinzel",serif;font-weight:600;font-size:24px;color:var(--red);letter-spacing:.5px}
.top-btn{top:20px;height:47px;display:flex;align-items:center;justify-content:center;font-family:"Cinzel",serif;font-weight:600;font-size:17px;border:2px solid var(--red)}
.btn-home{left:727px;width:94px;color:var(--red);background:#fff}
.btn-contact{left:836px;width:119px;color:#fff;background:var(--red)}
.btn-login{left:969px;width:119px;color:#fff;background:var(--red);gap:5px}
.navbar{left:350px;top:85px;width:850px;height:47px;background:var(--dark);clip-path:polygon(28px 0,100% 0,100% 100%,0 100%)}
.nav{left:380px;top:85px;height:47px;display:flex;align-items:center;gap:0}
.nav a{color:#fff;text-decoration:none;font-size:15.5px;font-weight:700;padding:0 18px;position:relative;height:47px;display:flex;align-items:center}
.nav a.active::after{content:"";position:absolute;left:20px;right:20px;bottom:0;height:3px;background:#fff}

/* hero */
.hero{left:0;top:132px;width:1200px;height:600px;background:linear-gradient(180deg,#0f1d33 0%,#2a2a3a 35%,#6b1d14 60%,#2b1a18 80%,#141414 100%)}
.hero-glow{left:520px;top:132px;width:680px;height:600px;background:radial-gradient(ellipse at 50% 40%,rgba(214,52,30,.55),rgba(214,52,30,0) 70%)}
.hero-title{left:180px;top:312px;width:840px;text-align:center;color:#fff;font-family:"Poppins",sans-serif;font-weight:500;font-size:46px;line-height:60px}
.search{left:304px;top:468px;width:591px;height:54px;background:#fff;border-radius:5px;display:flex;align-items:center;padding:0 4px 0 22px}
.search span{flex:1;font-style:italic;font-size:12px;color:#999}
.search b{width:108px;height:46px;background:var(--red);color:#fff;font-family:"Poppins",sans-serif;font-weight:600;font-size:17px;display:flex;align-items:center;justify-content:center;border-radius:4px}
.arrow{top:410px}

/* intro */
.intro-shadow{left:120px;top:834px;width:455px;height:384px;background:var(--red)}
.intro-photo{left:111px;top:825px;width:455px;height:384px;background:linear-gradient(160deg,#b9d4ec 0%,#e8e3d4 40%,#c9b9a0 65%,#5f7f3c 100%)}
.intro-sign{left:385px;top:960px;width:181px;height:190px;background:var(--red)}
.intro-h{left:643px;top:815px;width:480px;font-family:"Cinzel",serif;font-weight:500;font-size:33px;line-height:42px;color:var(--ink)}
.intro-p{left:643px;top:958px;width:440px;font-size:15px;line-height:25.7px;color:var(--text)}
.btn-red{display:flex;align-items:center;justify-content:center;background:var(--red);color:#fff;font-family:"Cinzel",serif;font-weight:600;font-size:15px;border-radius:3px}
.intro-btn{left:643px;top:1160px;width:129px;height:46px}

/* mortgage */
.band{left:0;top:1311px;width:1200px;height:386px;background:linear-gradient(120deg,#b0262b 0%,#c93a3c 45%,#a3181d 100%)}
.rates{left:290px;top:1417px;width:620px;height:421px;background:#fff;border-radius:8px;box-shadow:0 4px 18px rgba(0,0,0,.12);font-family:"Poppins",sans-serif}
.rates-head{position:absolute;left:9px;top:8px;width:602px;height:66px;background:var(--red);border-radius:6px 6px 0 0;color:#fff;font-weight:600;font-size:21px;display:flex;align-items:center;justify-content:center}
.rates-sub{position:absolute;left:9px;top:74px;width:602px;height:80px;background:var(--pink);font-weight:500;font-size:19px}
.rates-sub span{position:absolute;top:26px}
.rates-row{position:absolute;left:78px;width:500px;font-size:18.5px;color:var(--ink)}
.rates-row span:last-child{position:absolute;left:362px}
.rates-foot{position:absolute;left:0;top:360px;width:620px;border-top:1px solid #e3e3e3;text-align:center;padding-top:16px;font-size:19px}

/* listings */
.sec-title{left:0;top:1920px;width:1200px;text-align:center;font-family:"Cinzel",serif;font-weight:500;font-size:34px}
.card{top:1999px;width:481px;height:459px;border:1px solid #ddd;background:#fff}
.card-photo{position:absolute;left:0;top:0;width:479px;height:218px}
.card-title{position:absolute;left:39px;top:246px;width:380px;font-family:"Cinzel",serif;font-weight:500;font-size:20px;line-height:29px}
.card-meta{position:absolute;left:39px;top:322px;display:flex;align-items:center;gap:10px;font-size:14px;color:#555}
.card-type{position:absolute;right:50px;top:329px;font-size:14px;color:var(--muted)}
.card-btn{position:absolute;left:39px;top:374px;width:131px;height:43px}

/* footer */
.footer{left:0;top:2552px;width:1200px;height:427px;background:var(--dark)}
.foot-brand{left:450px;top:2630px;width:300px;display:flex;flex-direction:column;align-items:center;gap:14px}
.foot-brand .brand-mark{background:#fff;width:40px;height:40px}
.foot-brand .brand-name{color:#fff;font-size:30px}
.foot-nav{left:0;top:2772px;width:1200px;display:flex;justify-content:center;gap:33px;color:#fff;font-size:16px}
.social{top:2820px;width:40px;height:40px;border-radius:50%;background:var(--red)}
.foot-rule{left:108px;top:2908px;width:984px;height:1px;background:#444}
.badge{top:2930px;background:#fff}
.copy{left:446px;top:2937px;color:#fff;font-size:12px}
.code{left:1114px;top:2937px;color:#fff;font-size:11px}
</style>
</head>
<body>

<header>
  <div class="abs brand"><div class="brand-mark"></div><div class="brand-name">BRIGHTHOLD</div></div>
  <div class="abs top-btn btn-home">HOME</div>
  <div class="abs top-btn btn-contact">CONTACT</div>
  <div class="abs top-btn btn-login">
    <svg width="15" height="15" viewBox="0 0 16 16"><circle cx="8" cy="8" r="7.5" fill="#fff"/><circle cx="8" cy="6" r="2.6" fill="#9e1016"/><path d="M3.3 12.6c1.2-2 2.8-2.8 4.7-2.8s3.5.8 4.7 2.8" fill="#9e1016"/></svg>LOG IN
  </div>
  <div class="abs navbar"></div>
  <nav class="abs nav">
    <a class="active">Listings</a><a>Owners</a><a>Prospect</a><a>Tenants</a><a>About</a><a>Community</a><a>Mortgage Info</a>
  </nav>
</header>

<section>
  <div class="abs hero" role="img" aria-label="Night view of a lit red lift bridge and city skyline over a river"></div>
  <div class="abs hero-glow"></div>
  <h1 class="abs hero-title">Get 1 Month Property Management Fee Off. $120 Value!!</h1>
  <svg class="abs arrow" style="left:68px" width="26" height="46" viewBox="0 0 26 46"><path d="M22 4 4 23l18 19" fill="none" stroke="#fff" stroke-width="4"/></svg>
  <svg class="abs arrow" style="left:1106px" width="26" height="46" viewBox="0 0 26 46"><path d="M4 4l18 19L4 42" fill="none" stroke="#fff" stroke-width="4"/></svg>
  <div class="abs search"><span>Enter address, city, zip, neighborhood or #MLS</span><b>Search</b></div>
</section>

<section>
  <div class="abs intro-shadow"></div>
  <div class="abs intro-photo" role="img" aria-label="Two-story suburban house with a red For Rent sign on the lawn"></div>
  <div class="abs intro-sign"></div>
  <h2 class="abs intro-h">Property Management Elk Grove, Sacramento &amp; Surrounding Areas</h2>
  <p class="abs intro-p">Having the right property manager means having an agent who is committed to helping you and making being a home provider hassle free. I believe clear communication, work ethic, time management, staying focused and knowledge goes a long way in my business. This commitment level has helped us build a remarkable track record of delivering results and maintaining a long lasting business partnership with our clients.</p>
  <div class="abs btn-red intro-btn">LEARN MORE</div>
</section>

<section>
  <div class="abs band" role="img" aria-label="Red-tinted photo of a small model house on paperwork"></div>
  <div class="abs rates">
    <div class="rates-head">Mortgage Rates</div>
    <div class="rates-sub"><span style="left:69px">National</span><span style="left:431px;top:28px">Average Rate</span></div>
    <div class="rates-row" style="top:176px"><span>30-Year FHA Rate</span><span>7.07%</span></div>
    <div class="rates-row" style="top:219px"><span>30-Year Fixed Rate</span><span>5.88%</span></div>
    <div class="rates-row" style="top:262px"><span>20-Year Fixed Rate</span><span>7.19%</span></div>
    <div class="rates-row" style="top:305px"><span>15-Year Fixed Rate</span><span>6.61%</span></div>
    <div class="rates-foot">Information updated: 6/13/2024</div>
  </div>
</section>

<section>
  <h2 class="abs sec-title">Featured Listings</h2>
  <div class="abs card" style="left:108px">
    <div class="card-photo" role="img" aria-label="Single-story beige house with autumn trees" style="background:linear-gradient(180deg,#8db6e0 0%,#c9c09a 40%,#d8d1c0 70%,#7d6a55 100%)"></div>
    <div class="card-meta">
      <svg width="26" height="22" viewBox="0 0 26 22"><path d="M3 3v11h20v-3H6M3 14v4M23 14v4M2 18h22" fill="none" stroke="#777" stroke-width="1.4"/></svg>1 &nbsp;|&nbsp;
      <svg width="24" height="20" viewBox="0 0 24 20"><rect x="3" y="3" width="18" height="12" rx="2" fill="none" stroke="#777" stroke-width="1.4"/><path d="M3 10h18M5 15v3M19 15v3" stroke="#777" stroke-width="1.4"/></svg>0
    </div>
    <div class="card-type">Residential</div>
    <div class="btn-red card-btn">VIEW MORE</div>
  </div>
  <div class="abs card" style="left:611px">
    <div class="card-photo" role="img" aria-label="Small tan ADU unit beside a large tree" style="background:linear-gradient(180deg,#9cc3e6 0%,#b8cde0 35%,#d9b794 60%,#6e5b45 100%)"></div>
    <div class="card-title">Fantastic opportunity 2 Bdrm x 1 Bth ADU Unit!!</div>
    <div class="card-meta">
      <svg width="26" height="22" viewBox="0 0 26 22"><path d="M3 3v11h20v-3H6M3 14v4M23 14v4M2 18h22" fill="none" stroke="#777" stroke-width="1.4"/></svg>1 &nbsp;|&nbsp;
      <svg width="24" height="20" viewBox="0 0 24 20"><rect x="3" y="3" width="18" height="12" rx="2" fill="none" stroke="#777" stroke-width="1.4"/><path d="M3 10h18M5 15v3M19 15v3" stroke="#777" stroke-width="1.4"/></svg>2
    </div>
    <div class="card-type">Residential</div>
    <div class="btn-red card-btn">VIEW MORE</div>
  </div>
</section>

<footer>
  <div class="abs footer"></div>
  <div class="abs foot-brand"><div class="brand-mark"></div><div class="brand-name">BRIGHTHOLD</div></div>
  <nav class="abs foot-nav"><span>Listings</span><span>Owners</span><span>Prospect</span><span>Tenants</span><span>About</span><span>Community</span><span>Mortgage Info</span></nav>
  <div class="abs social" style="left:514px"></div>
  <div class="abs social" style="left:558px"></div>
  <div class="abs social" style="left:602px"></div>
  <div class="abs social" style="left:646px"></div>
  <div class="abs foot-rule"></div>
  <div class="abs badge" style="left:111px;width:41px;height:30px"></div>
  <div class="abs badge" style="left:179px;width:68px;height:28px"></div>
  <div class="abs badge" style="left:275px;width:24px;height:28px"></div>
  <div class="abs copy">©Copyrights 2024 Brighthold &nbsp;| &nbsp; All Rights Reserved</div>
  <div class="abs code">C51</div>
</footer>

</body>
</html>
```